Now Leasing Banner

Looking for a banner that says the following information approx 4' x 30'

Now Leasing Maplebrook Terrace 925-318-6042

Target Market(s)

Drive by traffic

Industry/Entity Type

Residential property management

Requirements
Must have
• Clear and readable from a distance

```html
<!DOCTYPE html>
<html lang="en">
<head>
<meta charset="utf-8">
<title>Now Leasing Banner</title>
<link href="https://fonts.googleapis.com/css2?family=Outfit:wght@500&display=swap" rel="stylesheet">
<style>
  :root {
    --sky-top: #5d6b80;
    --sky-low: #6e7a88;
    --horizon: #3b4a58;
    --town: #4a4e4c;
    --hill-green: #3f6a2c;
    --hill-dark: #2d4a22;
    --text: #ffffff;
    --shade: rgba(20, 24, 30, 0.35);
  }
  html, body {
    margin: 0;
    padding: 0;
    overflow: hidden;
    background: #ffffff;
  }
  .banner {
    position: relative;
    width: 1200px;
    height: 240px;
    overflow: hidden;
    font-family: "Outfit", "Helvetica Neue", Arial, sans-serif;
    color: var(--text);
  }
  .banner__scene {
    position: absolute;
    inset: 0;
    background:
      linear-gradient(to bottom,
        var(--sky-top) 0%,
        var(--sky-low) 30%,
        var(--horizon) 38%,
        var(--town) 52%,
        var(--hill-green) 78%,
        var(--hill-dark) 100%);
  }
  .banner__shade {
    position: absolute;
    inset: 0;
    background: var(--shade);
  }
  .banner__content {
    position: absolute;
    inset: 0;
    display: flex;
    flex-direction: column;
    align-items: center;
  }
  .banner__headline {
    margin: 38px 0 0;
    font-weight: 500;
    font-size: 58px;
    line-height: 1;
    letter-spacing: 0.5px;
    white-space: nowrap;
  }
  .banner__phone {
    display: flex;
    align-items: center;
    gap: 22px;
    margin-top: 40px;
    font-weight: 500;
    font-size: 58px;
    line-height: 1;
    letter-spacing: 1px;
  }
  .banner__phone-icon {
    width: 64px;
    height: 64px;
  }
</style>
</head>
<body>
  <section class="banner">
    <div class="banner__scene" role="img" aria-label="Aerial view of a hillside residential neighborhood with green hills under a blue sky"></div>
    <div class="banner__shade"></div>
    <div class="banner__content">
      <h1 class="banner__headline">Now Leasing Maplebrook Terrace</h1>
      <p class="banner__phone">
        <svg class="banner__phone-icon" viewBox="0 0 64 64" fill="none" stroke="#ffffff" stroke-width="3" stroke-linecap="round" stroke-linejoin="round" aria-hidden="true">
          <path d="M14 6 l9 2 l4 13 l-6 5 c4 8 9 13 17 17 l5 -6 l13 4 l2 9 c-1 5 -5 8 -10 8 C26 56 8 38 6 16 c0 -5 3 -9 8 -10 z"/>
          <path d="M36 16 a12 12 0 0 1 12 12"/>
          <path d="M36 6 a22 22 0 0 1 22 22"/>
        </svg>
        <span class="banner__phone-number">925-318-6042</span>
      </p>
    </div>
  </section>
</body>
</html>
```